Postcard design to acquire new clients for my Property Management Company

I'm looking for a postcard design that I can send to prospective clients detailing information about my company and services.
Postcard should be eye catching and contain information from www.bramblecrestpm.com. I've provided a few screen shots for the most important information and my logo.
Target Market(s)
Real Estate
Industry/Entity Type
Real Estate
Font styles to use
Sans Serif
Requirements
Must have
- Must be eye catching!! this will be a direct mail piece - I'd like for the card to be read and not tossed in the trash immediately.
Design que from the logo.
A place to write / print the receipts name and address.
our physical address - 2387 Hollow Pine Road, Lubbock, TX 79852.
Should not have
- the contact information on the business card is not accurate - please use info from website.

```html
<!DOCTYPE html>
<html lang="en">
<head>
<meta charset="utf-8">
<title>Bramblecrest Property Management – Postcard</title>
<link href="https://fonts.googleapis.com/css2?family=Arimo:wght@400;700&display=swap" rel="stylesheet">
<style>
  :root{
    --navy:#1d4e86;
    --navy-dark:#1a477c;
    --ink:#222;
    --paper:#ffffff;
    --bg:#efefef;
    --rule:#333;
    --photo-a:#c9ccc8;
    --photo-b:#e8e6e2;
  }
  *{box-sizing:border-box;margin:0;padding:0}
  html,body{width:1200px;height:1199px;overflow:hidden;background:var(--bg);font-family:"Arimo",Arial,sans-serif;color:var(--ink)}
  .card{position:absolute;left:210px;width:780px;height:545px;background:var(--paper);box-shadow:4px 4px 8px rgba(0,0,0,.35);overflow:hidden}
  .card--front{top:40px}
  .card--back{top:614px}

  /* front */
  .front-art{position:absolute;left:0;top:0;width:400px;height:545px}
  .brand{position:absolute;left:293px;top:32px;color:var(--navy);font-weight:400}
  .brand-name{font-size:31px;letter-spacing:5px;line-height:1}
  .brand-sub{font-size:14px;letter-spacing:3.6px;margin-top:6px}
  .headline{position:absolute;left:293px;top:122px;color:var(--navy);font-weight:700;font-size:24.5px;line-height:31px}
  .tagline{position:absolute;left:293px;top:188px;font-size:13.5px}
  .plan{position:absolute;display:flex;gap:10px}
  .plan-meta{width:130px}
  .plan-title{font-size:18px;line-height:21px}
  .plan-note{font-size:11.5px}
  .plan-rate{font-size:24px;font-weight:700;color:var(--navy);margin-top:3px;line-height:27px}
  .plan-basis{font-size:11.5px}
  .plan-features{font-size:11px;line-height:14.5px;padding-top:28px;white-space:nowrap}
  .plan--lease{left:308px;top:216px}
  .plan--full{left:353px;top:322px}
  .plan--premium{left:402px;top:430px}

  /* back */
  .services{position:absolute;left:0;top:0;width:390px;height:545px;background:var(--navy);color:#fff}
  .services-title{position:absolute;left:0;width:390px;text-align:center;top:32px;font-size:25px;font-weight:700}
  .services-sub{position:absolute;left:0;width:390px;text-align:center;top:65px;font-size:13.5px}
  .service{position:absolute;display:flex;align-items:center;gap:8px;font-size:21px}
  .service svg{width:34px;height:34px;flex:none}
  .contact{position:absolute;left:16px;top:497px;font-size:18.5px}
  .contact b{font-weight:700}
  .stamp-box{position:absolute;left:647px;top:36px;width:94px;height:94px;border:1.5px solid var(--rule)}
  .address-line{position:absolute;left:410px;width:345px;border-top:1.5px solid var(--rule)}
</style>
</head>
<body>

<section class="card card--front">
  <svg class="front-art" viewBox="0 0 400 545">
    <defs>
      <linearGradient id="photoTone" x1="0" y1="0" x2="1" y2="1">
        <stop offset="0" stop-color="var(--photo-a)"/>
        <stop offset="1" stop-color="var(--photo-b)"/>
      </linearGradient>
    </defs>
    <polygon points="0,0 158,0 388,545 0,545" fill="url(#photoTone)" role="img" aria-label="Photo of two hands sheltering a small white model house"/>
    <polygon points="158,0 168,0 398,545 388,545" fill="var(--navy)"/>
  </svg>

  <div class="brand">
    <div class="brand-name">BRAMBLECREST</div>
    <div class="brand-sub">PROPERTY MANAGEMENT</div>
  </div>

  <h1 class="headline">CHOOSE THE RIGHT PROPERTY<br>MANAGEMENT SYSTEM</h1>
  <p class="tagline">Selecting the wrong manager could be your costliest mistake ever.</p>

  <div class="plan plan--lease">
    <div class="plan-meta">
      <div class="plan-title">Lease Only</div>
      <div class="plan-note">You Just Need Tenants</div>
      <div class="plan-rate">9%</div>
      <div class="plan-basis">of annual lease</div>
    </div>
    <div class="plan-features">Professional Photography | Marketing &amp; Advertising<br>Property Showings | Tenant Screening &amp; Qualifications<br>Lease Execution | Move In Coordination</div>
  </div>

  <div class="plan plan--full">
    <div class="plan-meta" style="width:100px">
      <div class="plan-title">Full Service</div>
      <div class="plan-note">Our Most Popular</div>
      <div class="plan-rate">10%</div>
      <div class="plan-basis">of monthly rent</div>
    </div>
    <div class="plan-features" style="padding-top:14px">Includes Leasing Service | 24/7 Emergency Response<br>Move In &amp; Out Inspections | Professional Lease Enforcement<br>Schedule &amp; Oversee all Repairs | Pay all Invoices<br>Monthly &amp; Year End Statements | Annual Market Rent Analysis</div>
  </div>

  <div class="plan plan--premium">
    <div class="plan-meta" style="width:140px">
      <div class="plan-title">Premium Service</div>
      <div class="plan-note">Our Premier Service</div>
      <div class="plan-rate">12%</div>
      <div class="plan-basis">of monthly rent</div>
    </div>
    <div class="plan-features" style="padding-top:14px">Includes Full Service Features<br>Professional Video Marketing<br>Home Warranty Coordination<br>Tenant Retention Program</div>
  </div>
</section>

<section class="card card--back">
  <div class="services">
    <h2 class="services-title">Discover Our Services</h2>
    <p class="services-sub">We offer full-service property management solutions</p>

    <div class="service" style="left:14px;top:92px">
      <svg viewBox="0 0 34 34" fill="none" stroke="#fff" stroke-width="2"><circle cx="17" cy="17" r="15"/><path d="M9 17 L17 10 L25 17 M11 16 V24 H23 V16" /></svg>Property Marketing</div>
    <div class="service" style="left:88px;top:142px">
      <svg viewBox="0 0 34 34" fill="none" stroke="#fff" stroke-width="2"><circle cx="17" cy="17" r="15"/><circle cx="13" cy="14" r="3" fill="#fff"/><circle cx="21" cy="14" r="3" fill="#fff"/><path d="M8 23 Q13 17 17 23 Q21 17 26 23" fill="#fff"/></svg>Tenant Screening</div>
    <div class="service" style="left:14px;top:194px">
      <svg viewBox="0 0 34 34" fill="none" stroke="#fff" stroke-width="2"><circle cx="17" cy="17" r="15"/><path d="M21 11 H15 Q12 11 12 14 Q12 17 15 17 H19 Q22 17 22 20 Q22 23 19 23 H12 M17 8 V26"/></svg><span style="margin-left:6px">Rent Collection</span></div>
    <div class="service" style="left:88px;top:240px">
      <svg viewBox="0 0 34 34" fill="none" stroke="#fff" stroke-width="2"><circle cx="17" cy="17" r="15"/><path d="M12 24 L20 16 M17 11 L23 17 L25 13 L21 9 Z" fill="#fff"/></svg><span style="margin-left:12px">Maintenance</span></div>
    <div class="service" style="left:14px;top:286px">
      <svg viewBox="0 0 34 34" fill="none" stroke="#fff" stroke-width="2"><circle cx="17" cy="17" r="15"/><circle cx="15" cy="15" r="5"/><path d="M19 19 L24 24" stroke-width="3"/></svg><span style="margin-left:6px">Property Inspections</span></div>
    <div class="service" style="left:88px;top:336px">
      <svg viewBox="0 0 34 34" fill="none" stroke="#fff" stroke-width="2"><circle cx="17" cy="17" r="15"/><path d="M10 23 H24 M12 21 V16 M15 21 V13 M18 21 V17 M21 21 V12" stroke-width="1.6"/></svg><span style="margin-left:12px">Financial Reporting</span></div>
    <div class="service" style="left:14px;top:389px">
      <svg viewBox="0 0 34 34" fill="none" stroke="#fff" stroke-width="2"><circle cx="17" cy="17" r="15"/><path d="M17 9 L24 11 Q24 21 17 25 Q10 21 10 11 Z"/><path d="M17 12 V22 Q13 19 13 13 Z" fill="#fff" stroke="none"/></svg><span style="margin-left:6px">Evictions</span></div>
    <div class="service" style="left:88px;top:434px">
      <svg viewBox="0 0 34 34" fill="none" stroke="#fff" stroke-width="1.8"><circle cx="17" cy="17" r="15"/><path d="M17 9 V24 M12 24 H22 M10 12 H24 M10 12 L8 18 H12 Z M24 12 L22 18 H26 Z"/></svg><span style="margin-left:12px">Legal Guidance</span></div>

    <p class="contact"><b>(806) 555-0147</b> | info@bramblecrestpm.com</p>
  </div>

  <div class="stamp-box"></div>
  <div class="address-line" style="top:290px"></div>
  <div class="address-line" style="top:349px"></div>
  <div class="address-line" style="top:408px"></div>
  <div class="address-line" style="top:467px"></div>
</section>

</body>
</html>
```